I have a website called Okenta Holdings (okentaholdings.com) that I would like to have redesigned. Most of the content is already created, but I need a new design. You can also see my other website at brambleacres.com. I am open to a new logo or modifying the current logo if you have a good idea. Please feel free to use other images for the home page (and maybe some other locations) if you feel they provide a better look and feel to the website. I prefer a modern look.

Important: You do not have to use the images I've provided for the home page. Feel free to find your own stock photos. You don't have to pay for them unless I select your design.

1) Please use wix.com to make your changes so that I can edit it later.
2) I will need all the graphics files to be saved so I can dowload it for later.
3) I will be adding more content to the site later.
4) This site will likely be transferred over to brambleacres.com so if you make a logo please make one for Okenta Holdings and one for Bramble Acres.
5) You can use other images that you feel would help the look and feel of the website.

```html
<!DOCTYPE html>
<html lang="en">
<head>
<meta charset="utf-8">
<title>Bramble Acres</title>
<link href="https://fonts.googleapis.com/css2?family=Inter+Tight:wght@400;500;600;700&display=swap" rel="stylesheet">
<style>
:root{
  --blue:#3a87d9;
  --blue-light:#4a9bf0;
  --navy:#0d4f9e;
  --ink:#2b2b2b;
  --muted:#6a6a6a;
  --white:#ffffff;
  --footer:#1b1b1d;
  --star:#f29a1a;
  --rule:#d9d9d9;
}
*{margin:0;padding:0;box-sizing:border-box}
html,body{width:1200px;height:3674px;overflow:hidden}
body{position:relative;font-family:"Inter Tight",Arial,sans-serif;color:var(--ink);background:var(--white);letter-spacing:-0.01em}
.abs{position:absolute}
.btn{position:absolute;display:flex;align-items:center;justify-content:center;background:var(--blue);color:var(--white);border-radius:8px;font-size:19px;font-weight:500}

/* hero */
.hero{left:0;top:0;width:1200px;height:852px;background:radial-gradient(ellipse at 30% 40%,#6a3a4a 0%,#3a3550 35%,#1d2a3c 75%,#162031 100%)}
.hero-shade{left:0;top:0;width:1200px;height:852px;background:linear-gradient(180deg,rgba(10,15,30,.55) 0%,rgba(10,15,30,.15) 40%,rgba(10,15,30,.45) 100%)}
.logo{left:83px;top:44px;display:flex;align-items:center;gap:12px;color:var(--white);font-size:27px;font-weight:700}
.logo-mark{width:34px;height:34px;background:var(--blue-light);border-radius:4px}
.nav{left:438px;top:56px;display:flex;gap:34px;color:var(--white);font-size:18px}
.btn-contact{left:965px;top:37px;width:152px;height:63px;font-size:19px}
.nav-rule{left:83px;top:121px;width:1034px;height:1px;background:rgba(255,255,255,.45)}
.hero-title{left:0;top:268px;width:1200px;text-align:center;font-size:86px;font-weight:600;line-height:72px;letter-spacing:-0.05em;color:var(--white)}
.hero-title span{display:block;color:var(--blue-light)}
.hero-sub{left:0;top:448px;width:1200px;text-align:center;color:var(--white);font-size:27px;line-height:30px;letter-spacing:-0.03em}
.btn-start{left:512px;top:541px;width:174px;height:63px}
.partners{left:0;top:752px;width:1200px;height:100px;background:rgba(150,155,165,.55);display:flex;align-items:center;color:var(--white)}
.partners-label{margin-left:143px;font-size:23px;font-weight:500;padding-right:40px;border-right:3px solid var(--white);line-height:44px}
.partner{font-size:25px;font-weight:600;margin-left:46px}

/* about */
.about-photo{left:83px;top:939px;width:454px;height:441px;background:linear-gradient(135deg,#2a3f6a 0%,#46506a 40%,#7a7a3a 75%,#3a3520 100%)}
.about-title{left:588px;top:938px;font-size:40px;font-weight:600;line-height:36px;letter-spacing:-0.03em}
.about-title span{display:block;color:var(--navy)}
.about-body{left:588px;top:1038px;width:530px;font-size:19.5px;line-height:25px;color:var(--muted)}
.btn-learn{left:588px;top:1319px;width:184px;height:62px}
.section-rule{left:83px;top:1453px;width:1034px;height:1px;background:var(--rule)}

/* projects */
.section-title{left:0;width:1200px;text-align:center;font-size:40px;font-weight:600;letter-spacing:-0.03em}
.project-photo{top:1565px;width:327px;height:329px}
.project-name{top:1908px;font-size:20px;color:var(--muted)}

/* strategies */
.strategy-band{left:0;top:2080px;width:1200px;height:734px;background:linear-gradient(180deg,#4a5260 0%,#363c48 55%,#262b33 100%)}
.strategy-title{left:83px;top:2290px;font-size:66px;font-weight:600;line-height:58px;letter-spacing:-0.04em;color:var(--white)}
.strategy-title span{color:var(--blue-light)}
.btn-strat{left:84px;top:2558px;width:184px;height:62px}
.card{position:absolute;background:var(--white);border-radius:14px;box-shadow:0 14px 40px rgba(58,135,217,.18);padding:0 26px}
.card h3{color:var(--navy);font-size:28px;font-weight:600;text-align:center;letter-spacing:-0.03em;line-height:26px}
.card p{color:var(--muted);font-size:19px;line-height:25px}
.card ul{list-style:none;color:var(--muted);font-size:19px;line-height:35px}
.card li{position:relative;padding-left:30px}
.card li::before{content:"";position:absolute;left:12px;top:16px;width:4px;height:4px;border-radius:50%;background:var(--muted)}
.card ul.tight li{line-height:25px;margin-bottom:10px}
.card ul.tight li::before{top:11px}

/* testimonials */
.test-title{left:0;top:3016px;width:1200px;text-align:center;color:var(--blue);font-size:40px;font-weight:600;line-height:32px;letter-spacing:-0.04em}
.review{position:absolute;top:3108px;width:330px;height:234px;background:var(--white);border-radius:12px;box-shadow:0 6px 28px rgba(0,0,0,.08);padding:20px 19px}
.avatar{width:48px;height:46px;border-radius:3px}
.stars{position:absolute;right:20px;top:14px;color:var(--star);font-size:23px;letter-spacing:6px}
.review h4{margin-top:18px;font-size:20px;font-weight:600}
.review p{margin-top:10px;font-size:18px;line-height:24px;color:var(--muted)}
.arrow{position:absolute;top:3202px;width:42px;height:42px;border-radius:50%;background:var(--white);box-shadow:0 4px 16px rgba(0,0,0,.1);display:flex;align-items:center;justify-content:center}

/* footer */
.footer{left:0;top:3408px;width:1200px;height:266px;background:var(--footer);color:var(--white)}
.footer-head{left:83px;top:44px;font-size:20px;font-weight:600}
.footer-link{font-size:14px;font-weight:600}
</style>
</head>
<body>

<header>
  <div class="abs hero" role="img" aria-label="Aerial photo of a city construction site at dusk"></div>
  <div class="abs hero-shade"></div>
  <div class="abs logo"><span class="logo-mark"></span>Bramble Acres</div>
  <nav class="abs nav"><span>Home</span><span>About</span><span>Strategy</span><span>Projects</span></nav>
  <div class="btn btn-contact">Contact us</div>
  <div class="abs nav-rule"></div>
  <h1 class="abs hero-title">Building Together<span>Growing Together</span></h1>
  <p class="abs hero-sub">Private Commercial Real Estate<br>Investment And Development Firm</p>
  <div class="btn btn-start">Get Started</div>
  <div class="abs partners">
    <span class="partners-label">Corporate Partners</span>
    <span class="partner">Norvale</span>
    <span class="partner">Castrel</span>
    <span class="partner">Lumora</span>
    <span class="partner">Brightwell</span>
    <span class="partner">Ferncliff</span>
  </div>
</header>

<section class="about">
  <div class="abs about-photo" role="img" aria-label="Modern glass building with lit courtyard trees and stepping stones over water"></div>
  <h2 class="abs about-title">About<span>Bramble Acres</span></h2>
  <p class="abs about-body">Bramble Acres is a private real estate firm that specializes in the procurement, development, management, and disposition of various commercial real estate asset types including multifamily, industrial, single-family, hospitality, self-storage, and flex. The firm effectuates its strategy by utilizing long-standing relationships to ascertain acquisition and development opportunities within a specific target market. Bramble Acres is currently focused on acquisition and development opportunities in the southern portion of the United States.</p>
  <div class="btn btn-learn">Learn More</div>
  <div class="abs section-rule"></div>
</section>

<section class="projects">
  <h2 class="abs section-title" style="top:1497px">Top Projects</h2>
  <div class="abs project-photo" style="left:83px;background:linear-gradient(160deg,#c9d7e6 0%,#d8cbb3 45%,#7d8f5a 80%,#6e6e6e 100%)" role="img" aria-label="Rendering of a mid-rise residential building with landscaped street"></div>
  <div class="abs project-photo" style="left:435px;background:linear-gradient(180deg,#dfe6ec 0%,#8a8278 40%,#7ea45c 75%,#c9c9c9 100%)" role="img" aria-label="Rendering of a residential complex with courtyard lawn"></div>
  <div class="abs project-photo" style="left:789px;background:linear-gradient(180deg,#1f5fc4 0%,#3a7ad8 30%,#e6e6e6 55%,#cfcfcf 85%,#8b8b8b 100%)" role="img" aria-label="White industrial warehouse building under a blue sky"></div>
  <p class="abs project-name" style="left:83px">Stonebay Harbor Residences</p>
  <p class="abs project-name" style="left:435px">Willowmere in Alder Creek</p>
  <p class="abs project-name" style="left:789px">Meridian Industrial</p>
</section>

<section class="strategies">
  <div class="abs strategy-band" role="img" aria-label="Photo of a modern multifamily apartment building at dusk"></div>
  <h2 class="abs strategy-title">Motives and<br>strategies of<br><span>Bramble<br>Acres</span></h2>
  <div class="btn btn-strat">Our Strategies</div>

  <div class="card" style="left:803px;top:2045px;width:324px;height:399px;padding-top:24px">
    <h3>Development</h3>
    <p style="margin-top:36px">Site Selection:</p>
    <ul class="tight"><li>Undeveloped Land</li><li>Entitled Land</li><li style="margin-bottom:0">Urban Redevelopment</li></ul>
    <p>Multiple Construction Types:</p>
    <ul class="tight"><li>Single Story Garden</li><li>Wrap Construction</li><li>Podium Construction</li><li>Tiltwall</li></ul>
  </div>

  <div class="card" style="left:542px;top:2329px;width:246px;height:328px;padding-top:34px">
    <h3>Product Types</h3>
    <ul style="margin-top:18px"><li>Multifamily</li><li>Industrial</li><li>SFR Communities</li><li>Self-Storage</li><li>Hospitality</li><li>Retail</li></ul>
  </div>

  <div class="card" style="left:803px;top:2464px;width:324px;height:327px;padding-top:38px">
    <h3>Acquisitions:<br>Distressed/Value-Add</h3>
    <ul class="tight" style="margin-top:28px;padding-right:4px"><li>Assets which yeild cash-on-cash returns as well as rent growth and exit upside.</li><li>Major Metropolitan Areas</li><li>Asset Value between $10 - $75mm</li></ul>
  </div>

  <div class="card" style="left:498px;top:2691px;width:290px;height:243px;padding-top:30px">
    <h3>Investment Focus</h3>
    <ul style="margin-top:16px"><li>Ground-up Development</li><li>Value-Add Acquisition</li><li>Equity Financing</li><li>Debt Financing</li></ul>
  </div>
</section>

<section class="testimonials">
  <h2 class="abs test-title">Our work and quality<br>speak for themselves</h2>
  <div class="arrow" style="left:27px"><svg width="20" height="20" viewBox="0 0 20 20"><path d="M16 10H4M9 5l-5 5 5 5" fill="none" stroke="#3a87d9" stroke-width="2"/></svg></div>
  <div class="arrow" style="left:1132px"><svg width="20" height="20" viewBox="0 0 20 20"><path d="M4 10h12M11 5l5 5-5 5" fill="none" stroke="#3a87d9" stroke-width="2"/></svg></div>

  <div class="review" style="left:84px">
    <div class="avatar" style="background:#e8a53a" role="img" aria-label="Reviewer portrait"></div>
    <div class="stars">★★★★☆</div>
    <h4>Mara Holt</h4>
    <p>Amet minim mollit non deserunt ullamco est sit aliqua dolor do amet sint. Velit officia consequat duis enim velit mollit....</p>
  </div>
  <div class="review" style="left:435px">
    <div class="avatar" style="background:#7fb8d8" role="img" aria-label="Reviewer portrait"></div>
    <div class="stars">★★★★☆</div>
    <h4>Dev Castellan</h4>
    <p>ullamco est sit aliqua dolor do amet sint. Velit officia consequat duis enim velit mollit. Exercitation veniam consequat sunt nostrud...</p>
  </div>
  <div class="review" style="left:786px">
    <div class="avatar" style="background:#e2b23c" role="img" aria-label="Reviewer portrait"></div>
    <div class="stars">★★★★☆</div>
    <h4>Ines Marlow</h4>
    <p>Amet minim mollit non deserunt ullamco est sit aliqua dolor do amet sint. Velit officia consequat duis enim velit mollit....</p>
  </div>
</section>

<footer class="abs footer">
  <p class="abs footer-head">Header Text</p>
  <span class="abs footer-link" style="left:83px;top:106px">Button</span>
  <span class="abs footer-link" style="left:345px;top:106px">Button</span>
  <span class="abs footer-link" style="left:608px;top:106px">Button</span>
  <span class="abs footer-link" style="left:870px;top:106px">Button</span>
  <span class="abs footer-link" style="left:83px;top:156px">Button</span>
  <span class="abs footer-link" style="left:345px;top:156px">Button</span>
  <span class="abs footer-link" style="left:608px;top:156px">Button</span>
  <span class="abs footer-link" style="left:870px;top:156px">Button</span>
  <span class="abs footer-link" style="left:83px;top:206px">Button</span>
  <span class="abs footer-link" style="left:345px;top:206px">Button</span>
  <span class="abs footer-link" style="left:608px;top:206px">Button</span>
  <span class="abs footer-link" style="left:870px;top:206px">Button</span>
</footer>

</body>
</html>
```